Website für Geschenkartikel sucht ein Flyer Design
Zielgruppe
Wir vermitteln Geschenkartikel und Erlebnisgeschenke
Aufgabenstellung
Wir suchen ein Flyerdesign im Format Din Lang. Das Design sollte vielleicht etwas an unsere Website www.blauer-kieselweg.de angepasst sein. Es würde uns gefallen, wenn unser "Hauptbanner" integriert werden würde. Das Format sollte so sein, dass wir den Flyer gleich zum Druck weitergeben können.

```html
<!DOCTYPE html>
<html lang="de">
<head>
<meta charset="utf-8">
<title>Blauer Kieselweg – Flyer DIN lang</title>
<link rel="stylesheet" href="https://fonts.googleapis.com/css2?family=Roboto+Condensed:wght@400;600;700&display=swap">
<style>
  :root {
    --brand-red: #d0191c;
    --ink: #111111;
    --paper-top: #ffffff;
    --paper-bottom: #e6e6e6;
    --white: #ffffff;
    --photo-light: #f1f0ef;
    --photo-mid: #d9c2b8;
    --photo-dark: #6e6a68;
  }
  * { margin: 0; padding: 0; box-sizing: border-box; }
  html, body {
    width: 1200px;
    height: 2400px;
    overflow: hidden;
  }
  body {
    font-family: "Roboto Condensed", "Arial Narrow", sans-serif;
    color: var(--ink);
  }
  .flyer {
    position: relative;
    width: 1200px;
    height: 2400px;
    background: linear-gradient(180deg, var(--paper-top) 0%, var(--paper-top) 20%, var(--paper-bottom) 100%);
    overflow: hidden;
  }
  .top-band {
    position: absolute;
    left: 0; top: 0;
    width: 1200px; height: 277px;
    background: var(--brand-red);
    display: flex;
    align-items: center;
    justify-content: center;
  }
  .brand-title {
    color: var(--white);
    font-weight: 700;
    font-size: 100px;
    letter-spacing: 3px;
    word-spacing: 14px;
    line-height: 1;
  }
  .headline {
    position: absolute;
    left: 0; top: 340px;
    width: 1200px;
    text-align: center;
    font-weight: 700;
    font-size: 98px;
    line-height: 1.06;
  }
  .topic-cloud {
    position: absolute;
    left: 0; top: 0;
    width: 1200px; height: 1400px;
  }
  .topic-cloud text {
    font-family: "Roboto Condensed", "Arial Narrow", sans-serif;
    font-weight: 400;
    fill: var(--ink);
  }
  .gift-photo {
    position: absolute;
    left: 40px; top: 1345px;
    width: 1140px; height: 877px;
    background:
      radial-gradient(ellipse at 55% 30%, var(--photo-mid) 0%, rgba(217,194,184,0) 45%),
      radial-gradient(ellipse at 50% 85%, var(--photo-dark) 0%, rgba(110,106,104,0) 40%),
      linear-gradient(180deg, var(--photo-light), #dedbd9);
  }
  .bottom-band {
    position: absolute;
    left: 0; top: 2222px;
    width: 1200px; height: 178px;
    background: var(--brand-red);
    display: flex;
    align-items: center;
    justify-content: center;
  }
  .web-address {
    color: var(--white);
    font-weight: 600;
    font-size: 68px;
    letter-spacing: 1px;
  }
</style>
</head>
<body>
<main class="flyer">
  <header class="top-band">
    <h1 class="brand-title">BLAUER KIESELWEG</h1>
  </header>

  <h2 class="headline">Hier finden Sie immer<br>das passende Geschenk!</h2>

  <svg class="topic-cloud" viewBox="0 0 1200 1400" aria-label="Geschenkkategorien">
    <text x="130" y="741" font-size="73">Lustiges</text>
    <text x="751" y="778" font-size="113">Erlebnis</text>
    <text x="315" y="886" font-size="66">Personalisiertes</text>
    <text x="846" y="973" font-size="66">Poster</text>
    <text x="81" y="1072" font-size="114">Partner</text>
    <text x="486" y="1062" font-size="70">Freunde</text>
    <text x="784" y="1157" font-size="103">Kinder</text>
    <text x="85" y="1213" font-size="55">Textilien</text>
    <text x="340" y="1279" font-size="95">Elektronik</text>
    <text x="772" y="1312" font-size="55">Wohnaccesoirs</text>
  </svg>

  <div class="gift-photo" role="img" aria-label="Foto: lachende junge Frau mit ausgebreiteten Armen vor einem großen weißen Geschenkkarton mit altrosa Schleife"></div>

  <footer class="bottom-band">
    <p class="web-address">www.blauer-kieselweg.de</p>
  </footer>
</main>
</body>
</html>
```